Business card design

We need a business card designed completed for a new company. We are a company that works with associations, schools to convert their older text/DVDs into dynamic online and mobile programs. Our initial platform is designed for the legal associations and will enable their lawyers to access their content such as forms, videos, case law and support materials anywhere, anytime. We are also focused on Project Management Associations, Financial Management Associations and IT Associations.

I would like for the business card to have the following information:

Logo

Kent marrowby

President and CEO

kmarrowby@trevantiq.example

Mobile: 555-374-9160

www.trevantiq.example

Tag line: Transforming content into a mobile platform    

I would like it to be double sided, use the colours of the logo, tie into the mobile world

 

Industry/Entity Type

Legal

Logo Text

Trevantiq

```html
<!DOCTYPE html>
<html lang="en">
<head>
<meta charset="utf-8">
<title>Trevantiq business card</title>
<link rel="stylesheet" href="https://fonts.googleapis.com/css2?family=Open+Sans:wght@400;700&display=swap">
<style>
  :root {
    --backdrop: #ece9e4;
    --card-grey: #9a9a9a;
    --card-white: #ffffff;
    --band-dark: #676767;
    --band-light: #8d8d8d;
    --ink: #1f1f1f;
    --ink-soft: #555555;
    --paper-text: #ffffff;
    --label: #2a2a2a;
  }
  * { box-sizing: border-box; margin: 0; padding: 0; }
  html, body { width: 1200px; height: 800px; overflow: hidden; }
  body {
    background: var(--backdrop);
    font-family: "Open Sans", Arial, sans-serif;
    position: relative;
  }
  .side-label {
    position: absolute;
    font-size: 21px;
    color: var(--label);
    transform: translateX(-50%);
  }
  .card {
    position: absolute;
    width: 510px;
    height: 290px;
    border-radius: 22px;
    overflow: hidden;
    box-shadow: 0 6px 14px rgba(0,0,0,0.28);
  }
  .card--grey { background: var(--card-grey); }
  .card--white { background: var(--card-white); }
  .card__band { position: absolute; left: 0; top: 0; width: 510px; height: 290px; }
  .wordmark {
    position: absolute;
    left: 0; right: 0;
    text-align: center;
    font-weight: 700;
    letter-spacing: -1px;
    line-height: 1;
  }
  .card--grey .wordmark { color: var(--paper-text); }
  .card--white .wordmark { color: var(--ink-soft); }
  .wordmark--small { top: 52px; font-size: 58px; }
  .wordmark--large { top: 102px; font-size: 80px; }
  .contact-list {
    position: absolute;
    left: 80px; top: 151px;
    list-style: none;
    font-size: 12.5px;
    color: var(--ink);
    white-space: nowrap;
  }
  .contact-list li { display: flex; align-items: center; height: 21px; }
  .contact-list svg { width: 10px; height: 10px; margin-right: 6px; flex: none; fill: none; stroke: #444; stroke-width: 1.4; }
  .tagline {
    position: absolute;
    left: 294px; top: 176px;
    font-size: 15px;
    line-height: 20px;
    color: var(--ink);
    white-space: nowrap;
  }
  .name-line {
    position: absolute;
    left: 0; right: 0; top: 262px;
    text-align: center;
    color: var(--paper-text);
    font-size: 12px;
  }
  .name-line strong { font-size: 15px; }
  .web-line {
    position: absolute;
    left: 0; right: 0; top: 252px;
    text-align: center;
    font-size: 16px;
    letter-spacing: 3px;
    color: var(--ink);
  }
</style>
</head>
<body>

<span class="side-label" style="left:328px;top:50px">Front</span>
<span class="side-label" style="left:886px;top:50px">Back - 1</span>
<span class="side-label" style="left:332px;top:410px">Back - 2</span>
<span class="side-label" style="left:886px;top:410px">Back - 3</span>

<!-- front -->
<section class="card card--grey" style="left:73px;top:90px">
  <svg class="card__band" viewBox="0 0 510 290" aria-hidden="true">
    <path d="M0 264 Q255 236 510 264 L510 290 L0 290 Z" fill="var(--band-dark)"/>
    <path d="M0 258 Q255 228 510 258" fill="none" stroke="#ffffff" stroke-width="4"/>
  </svg>
  <div class="wordmark wordmark--small">Trevantiq</div>
  <ul class="contact-list">
    <li><svg viewBox="0 0 10 10"><rect x="2.5" y="0.8" width="5" height="8.4" rx="1"/></svg>555-374-9160</li>
    <li><svg viewBox="0 0 10 10"><rect x="0.8" y="2" width="8.4" height="6"/><path d="M0.8 2 L5 5.5 L9.2 2"/></svg>kmarrowby@trevantiq.example</li>
    <li><svg viewBox="0 0 10 10"><circle cx="5" cy="5" r="4.2"/><path d="M0.8 5 H9.2 M5 0.8 Q2 5 5 9.2 Q8 5 5 0.8"/></svg>www.trevantiq.example</li>
  </ul>
  <p class="tagline">Transforming content<br>into a mobile platform</p>
  <p class="name-line"><strong>Kent marrowby,</strong> President and CEO</p>
</section>

<!-- back 1 -->
<section class="card card--white" style="left:627px;top:90px">
  <svg class="card__band" viewBox="0 0 510 290" aria-hidden="true">
    <path d="M0 264 Q255 236 510 264 L510 290 L0 290 Z" fill="var(--band-dark)"/>
    <path d="M0 258 Q255 228 510 258" fill="none" stroke="var(--band-light)" stroke-width="4"/>
  </svg>
  <div class="wordmark wordmark--small">Trevantiq</div>
  <ul class="contact-list">
    <li><svg viewBox="0 0 10 10"><rect x="2.5" y="0.8" width="5" height="8.4" rx="1"/></svg>555-374-9160</li>
    <li><svg viewBox="0 0 10 10"><rect x="0.8" y="2" width="8.4" height="6"/><path d="M0.8 2 L5 5.5 L9.2 2"/></svg>kmarrowby@trevantiq.example</li>
    <li><svg viewBox="0 0 10 10"><circle cx="5" cy="5" r="4.2"/><path d="M0.8 5 H9.2 M5 0.8 Q2 5 5 9.2 Q8 5 5 0.8"/></svg>www.trevantiq.example</li>
  </ul>
  <p class="tagline">Transforming content<br>into a mobile platform</p>
  <p class="name-line"><strong>Kent marrowby,</strong> President and CEO</p>
</section>

<!-- back 2 -->
<section class="card card--grey" style="left:73px;top:452px">
  <div class="wordmark wordmark--large">Trevantiq</div>
  <p class="web-line">www.trevantiq.example</p>
</section>

<!-- back 3 -->
<section class="card card--white" style="left:634px;top:450px">
  <div class="wordmark wordmark--large">Trevantiq</div>
  <p class="web-line">www.trevantiq.example</p>
</section>

</body>
</html>
```